Business card for law firm

Need business card for new law firm. Think confident, authoritative, conservative, but not stuffy or old-fashioned.

Contact Information for Business Card

Content for card - logo (uploaded), plus the following:

Paul Whitcombe (larger font)
Managing Partner (larger font, but not as large as name)
Level 9, 7 Ferris Lane
Sydney NSW 2000
Main Tel 02 9364 2710
Direct Tel 02 8472 3159
Email paul@qvlegal.com.au
www.qvlegal.com.au

Letterhead design should include logo plus:
Level 9, 7 Ferris Lane
Sydney NSW 2000
Tel 02 8472 3159
www.qvlegal.com.au

```html
<!DOCTYPE html>
<html lang="en">
<head>
<meta charset="utf-8">
<title>Quayvale Legal — Business Card</title>
<link rel="stylesheet" href="https://fonts.googleapis.com/css2?family=Open+Sans:wght@400;600;700&display=swap">
<style>
  :root {
    --navy: #0d1f5c;
    --paper: #ffffff;
    --ink: #222222;
    --backdrop: #1e1e20;
    --rule: rgba(255,255,255,0.45);
  }
  * { box-sizing: border-box; margin: 0; padding: 0; }
  html, body {
    width: 1200px; height: 960px; overflow: hidden;
    background: var(--backdrop);
    font-family: "Open Sans", Arial, sans-serif;
  }
  .canvas { position: relative; width: 1200px; height: 960px; }

  .card {
    position: absolute; left: 240px;
    width: 720px; height: 440px;
    background: var(--paper);
    overflow: hidden;
    box-shadow: 0 12px 30px rgba(0,0,0,0.45);
  }
  .card--front { top: 30px; }
  .card--back { top: 490px; }

  /* Front */
  .brand-mark {
    position: absolute; left: 70px; top: 90px;
    width: 230px; height: 260px;
    background: var(--navy);
  }
  .brand-name {
    color: var(--navy);
    font-weight: 600;
    text-transform: uppercase;
    letter-spacing: 0.08em;
    white-space: nowrap;
  }
  .card--front .brand-name {
    position: absolute; left: 330px; top: 170px;
    font-size: 46px; line-height: 1;
  }
  .card--front .brand-name small {
    display: block; font-size: 46px;
    letter-spacing: 0.08em; margin-top: 6px;
  }
  .front-web {
    position: absolute; left: 332px; top: 300px;
    font-size: 15px; letter-spacing: 0.28em; color: var(--ink);
  }

  /* Back */
  .back-logo {
    position: absolute; left: 90px; top: 50px;
    display: flex; align-items: center; gap: 16px;
  }
  .back-logo .square { width: 54px; height: 54px; background: var(--navy); }
  .back-logo .brand-name { font-size: 34px; }

  .person {
    position: absolute; right: 50px; top: 160px; text-align: right;
  }
  .person-name {
    color: var(--navy); font-weight: 700; font-size: 22px;
    text-transform: uppercase; letter-spacing: 0.02em;
  }
  .person-role {
    color: #444; font-size: 15px; text-transform: uppercase; margin-top: 4px;
  }

  .contact-band {
    position: absolute; left: 0; right: 0; bottom: 0; height: 200px;
    background: var(--navy); color: #fff;
    display: flex; align-items: center;
    padding: 0 40px;
  }
  .contact-list { list-style: none; font-size: 16px; line-height: 1.75; }
  .contact-list li { display: flex; align-items: center; gap: 10px; }
  .contact-list svg { width: 16px; height: 16px; flex: none; }
  .band-divider {
    width: 1px; height: 90px; background: var(--rule); margin: 0 34px;
  }
  .address { font-style: normal; font-size: 17px; line-height: 1.6; }
</style>
</head>
<body>
<main class="canvas">

  <section class="card card--front" aria-label="Card front">
    <div class="brand-mark"></div>
    <div class="brand-name">Quayvale<small>Legal</small></div>
    <div class="front-web">www.qvlegal.com.au</div>
  </section>

  <section class="card card--back" aria-label="Card back">
    <div class="back-logo">
      <div class="square"></div>
      <div class="brand-name">Quayvale Legal</div>
    </div>

    <div class="person">
      <div class="person-name">Paul Whitcombe</div>
      <div class="person-role">Managing Partner</div>
    </div>

    <div class="contact-band">
      <ul class="contact-list">
        <li>
          <svg viewBox="0 0 16 16" aria-hidden="true"><path fill="#fff" d="M3.5 1.5l2.5 3-1.5 1.6c.8 1.8 2.2 3.2 4 4l1.6-1.5 3 2.5-1.3 2.4C6.8 13.2 2.8 9.2 1.1 2.8z"/></svg>
          02 9364 2710 (Main)
        </li>
        <li>
          <svg viewBox="0 0 16 16" aria-hidden="true"><path fill="#fff" d="M3.5 1.5l2.5 3-1.5 1.6c.8 1.8 2.2 3.2 4 4l1.6-1.5 3 2.5-1.3 2.4C6.8 13.2 2.8 9.2 1.1 2.8z"/></svg>
          02 8472 3159 (Direct)
        </li>
        <li>
          <svg viewBox="0 0 16 16" aria-hidden="true"><rect x="1" y="3.5" width="14" height="9" rx="1" fill="#fff"/><path d="M1.5 4l6.5 5 6.5-5" stroke="#0d1f5c" stroke-width="1.3" fill="none"/></svg>
          paul@qvlegal.com.au
        </li>
        <li>
          <svg viewBox="0 0 16 16" aria-hidden="true"><g fill="none" stroke="#fff" stroke-width="1.3"><circle cx="8" cy="8" r="6.3"/><ellipse cx="8" cy="8" rx="2.6" ry="6.3"/><path d="M1.8 8h12.4"/></g></svg>
          www.qvlegal.com.au
        </li>
      </ul>
      <div class="band-divider"></div>
      <address class="address">
        Level 9, 7 Ferris Lane<br>
        Sydney NSW 2000
      </address>
    </div>
  </section>

</main>
</body>
</html>
```